business card deign

Logo needs the following on it.
1. attached logo
2. Tagline - "If it keeps a drink cold or the party going...we do it!"
3. Name- Dalton Pikes, Founder and CPO
4. Address - 412 E. Carver Avenue, Ste 2207, Tampa, FL. 33917
5. Phone - 555.318.4726

```html
<!DOCTYPE html>
<html lang="en">
<head>
<meta charset="utf-8">
<title>Wallavo Business Card</title>
<link href="https://fonts.googleapis.com/css2?family=Arimo:ital,wght@0,400;0,700&display=swap" rel="stylesheet">
<style>
  :root {
    --backdrop: #e6e6e4;
    --card-light: #f4f4f3;
    --card-dark: #2b2b2b;
    --ink: #2a2a2a;
    --ink-soft: #666666;
    --rule: #555555;
    --paper: #ffffff;
    --paper-soft: #cfcfcf;
  }
  * { margin: 0; padding: 0; box-sizing: border-box; }
  html, body {
    width: 1200px;
    height: 801px;
    overflow: hidden;
    background: var(--backdrop);
    font-family: "Arimo", Arial, sans-serif;
  }
  .stage {
    position: relative;
    width: 1200px;
    height: 801px;
    display: flex;
    align-items: center;
    justify-content: center;
    gap: 40px;
  }
  .card {
    position: relative;
    width: 540px;
    height: 309px;
    box-shadow: 0 6px 18px rgba(0,0,0,0.12);
  }
  .card--front { background: var(--card-light); color: var(--ink); }
  .card--back { background: var(--card-dark); color: var(--paper); }

  .wordmark {
    display: flex;
    align-items: center;
    gap: 12px;
    font-weight: 700;
    letter-spacing: 0.42em;
    line-height: 1;
    white-space: nowrap;
  }
  .wordmark__mark {
    width: 14px;
    height: 14px;
    background: currentColor;
    flex: none;
  }
  .card--front .wordmark {
    position: absolute;
    right: 32px;
    top: 70px;
    font-size: 30px;
    color: var(--ink);
  }
  .card--back .wordmark {
    position: absolute;
    left: 50%;
    top: 132px;
    transform: translateX(-50%);
    font-size: 40px;
  }

  .tagline {
    position: absolute;
    left: 0;
    right: 0;
    top: 200px;
    text-align: center;
    font-size: 14px;
    letter-spacing: 0.04em;
    color: var(--paper-soft);
  }

  .long-rule {
    position: absolute;
    left: 250px;
    right: 40px;
    top: 160px;
    height: 1px;
    background: var(--rule);
  }
  .phone {
    position: absolute;
    right: 40px;
    top: 176px;
    display: flex;
    align-items: center;
    gap: 6px;
    font-size: 15px;
    font-weight: 700;
    color: var(--ink-soft);
  }
  .phone svg { width: 13px; height: 13px; fill: var(--ink-soft); }

  .contact {
    position: absolute;
    left: 40px;
    bottom: 34px;
  }
  .contact__name { font-size: 20px; font-weight: 700; color: var(--ink); }
  .contact__role { font-size: 15px; color: var(--ink-soft); margin-top: 2px; }
  .contact__rule { width: 190px; height: 1px; background: var(--rule); margin: 10px 0; }
  .contact__address { font-size: 14px; line-height: 1.35; color: var(--ink-soft); font-style: normal; }
</style>
</head>
<body>
  <main class="stage">
    <section class="card card--front">
      <div class="wordmark"><span class="wordmark__mark"></span>WALLAVO</div>
      <div class="long-rule"></div>
      <div class="phone">
        <svg viewBox="0 0 24 24" aria-hidden="true"><path d="M6.6 10.8a15.1 15.1 0 0 0 6.6 6.6l2.2-2.2c.3-.3.7-.4 1-.2 1.1.4 2.3.6 3.6.6.6 0 1 .4 1 1V20c0 .6-.4 1-1 1A17 17 0 0 1 3 4c0-.6.4-1 1-1h3.5c.6 0 1 .4 1 1 0 1.3.2 2.5.6 3.6.1.3 0 .7-.2 1z"/></svg>
        555.318.4726
      </div>
      <div class="contact">
        <div class="contact__name">Dalton Pikes</div>
        <div class="contact__role">Founder and CPO</div>
        <div class="contact__rule"></div>
        <address class="contact__address">412 E. Carver Avenue<br>Ste 2207, Tampa, FL. 33917</address>
      </div>
    </section>
    <section class="card card--back">
      <div class="wordmark"><span class="wordmark__mark"></span>WALLAVO</div>
      <p class="tagline">If it keeps a drink cold or the party going...we do it!</p>
    </section>
  </main>
</body>
</html>
```